Natural Light/Organic/Documentary Photography Business

I like a simple, approachable, feminine, earthy/organic feel. Earth/neutral tones, nothing too loud or obnoxious. I like the watercolor look. I don't want anything too trendy or something I'll get tired of after a couple months. As far as colors, I am much more a fan of cream/taupe/blue/green...not a fan of pink or purple at all.

Target Market(s)

Weddings & Families

Industry/Entity Type

Wedding Photography

Contact Information for Business Card

website, email, phone number

Font styles to use
Other font styles liked:
• Horizontes, Gotham

Colors

Designer to choose colors to be used in the design.

Requirements
Must have
• Website: www.mirelhatchway.com
• Phone: 418.629.5073
• Email: mirel@mirelhatchway.com
Nice to have
• I like the watercolor look but its not necessary. I like simple/earthy tones. Nothing too loud or distracting. Simple & feminine without being too girly. I like an approachable/soft feel.
• Instagram: www.instagram.com/mirelhatchwayphotography/
Should not have
• NO loud colors or design or pattern. I do not want a photo of a camera or lens or anything cheesy like that.

```html
<!DOCTYPE html>
<html lang="en">
<head>
<meta charset="utf-8">
<title>Mirel Hatchway Photography — Business Cards</title>
<link href="https://fonts.googleapis.com/css2?family=Lato:wght@300;400&display=swap" rel="stylesheet">
<style>
  :root {
    --backdrop: #8a8a8a;
    --card-white: #ffffff;
    --card-mist: #efefef;
    --ink: #3f3a36;
    --taupe: #8c7f76;
    --rule: #9a918a;
    --peach: #efc4a6;
    --cream: #efebe7;
    --mist-blue: #c9dcea;
  }
  * { margin: 0; padding: 0; box-sizing: border-box; }
  html, body { width: 1200px; height: 1200px; overflow: hidden; }
  body {
    position: relative;
    background: var(--backdrop);
    font-family: "Lato", "Helvetica Neue", Arial, sans-serif;
    color: var(--ink);
  }
  .card {
    position: absolute;
    top: 310px;
    height: 593px;
    overflow: hidden;
  }
  .card--front { left: 234px; width: 364px; background: var(--card-white); }
  .card--back  { left: 628px; width: 367px; background: var(--card-mist); }

  .wash {
    position: absolute;
    left: 0; right: 0;
    background: linear-gradient(100deg, var(--peach) 0%, var(--cream) 55%, var(--mist-blue) 100%);
  }
  .card--front .wash { top: 0; height: 472px; }
  .card--back .wash  { bottom: 0; height: 127px; }

  .wordmark {
    position: absolute;
    left: 0; right: 0;
    text-align: center;
    color: var(--taupe);
    font-weight: 300;
  }
  .wordmark__name {
    display: block;
    font-size: 38px;
    letter-spacing: 1px;
    line-height: 1;
  }
  .wordmark__tag {
    display: block;
    margin-top: 6px;
    font-size: 9px;
    letter-spacing: 5px;
    line-height: 1;
  }
  .card--front .wordmark { top: 496px; }
  .card--back .wordmark  { top: 122px; }

  .rule {
    position: absolute;
    left: 112px;
    width: 150px;
    height: 1px;
    background: var(--rule);
  }
  .rule--upper { top: 206px; }
  .rule--lower { top: 335px; }

  .contact {
    position: absolute;
    top: 228px;
    left: 0; right: 0;
    list-style: none;
    text-align: center;
    font-size: 20px;
    line-height: 24.5px;
  }
  .social {
    position: absolute;
    top: 366px;
    left: 0; right: 0;
    text-align: center;
    font-size: 16.5px;
  }
</style>
</head>
<body>
  <section class="card card--front">
    <div class="wash" role="img" aria-label="Watercolour texture area in soft peach, cream and blue tones"></div>
    <div class="wordmark">
      <span class="wordmark__name">Mirel Hatchway</span>
      <span class="wordmark__tag">PHOTOGRAPHY</span>
    </div>
  </section>

  <section class="card card--back">
    <div class="wordmark">
      <span class="wordmark__name">Mirel Hatchway</span>
      <span class="wordmark__tag">PHOTOGRAPHY</span>
    </div>
    <div class="rule rule--upper"></div>
    <ul class="contact">
      <li>418.629.5073</li>
      <li>mirel@mirelhatchway.com</li>
      <li>www.mirelhatchway.com</li>
    </ul>
    <div class="rule rule--lower"></div>
    <p class="social">instagram.com/mirelhatchwayphotography</p>
    <div class="wash" role="img" aria-label="Watercolour texture band in soft peach, cream and blue tones"></div>
  </section>
</body>
</html>
```